Spanish Student Needs a Cover for his PhD Dissertation

Hi everyone :) So, I'm a Corneal surgeon currently finishing my PhD, with a dissertation focused on the evaluation of quality of life in patients affected by a disease called Keratoconus. Just so you know, Keratoconus is a condition in which the cornea (the frontal part of the way) gets thin and bulgy and it decreases vision. What I did during my PhD was designing a questionnaire for evaluating quality of life in this kind of patients.
I need to design a hard cover for my dissertation, which is 200 sheets long. I like kind of minimalistic and geometric designs but I am totally open to suggestions. What needs to be in the cover is the name of the dissertation "Diseño, desarrollo y validación de una encuesta para evaluar el compromiso visual y emocional subjetivos en pacientes con Queratocono" and my name, "Iker Zurmendi". The other thing that needs to go there is the logo of my university (Universidad de Montehierro). Aside from that, anything else is up to the designer. It would be important to use the kind of "red" color I am using in the dissertation. I am attaching the frontal page of my dissertation so you know what kind of design and colors I am using.
In the back part, of the cover, there should be this small inscription: "Iker Zurmendi, MD, es un Oftalmólogo Subespecialista en Cirugía Refractiva de la Universidad Tecnológica Cordillerana (Colombia) y la Universidad de Montehierro (España). Actualmente se desempeña como miembro del Departamento de Córnea y Cirugía Refractiva de la Clínica de Oftalmología Miraluz y como director de su propia compañía de emprendimiento médico Silver Heron Surgical". Please leave a space to place my picture; I will have it taken this week so I don't have it right now, you can just leave the blank spot and I will include it later
The size of the pages is standard "letter" size.
Thanks a lot!

Target Market(s)

PhD Scholars

Font styles to use
Serif

Requirements
Must have
• The "red" color I use on my font. It must be formal but "young".
Nice to have
• I like to keep the design clean, kind of "formal with a young" touch so to speak. I really like gray colors, so it would be nice to have broad areas of gray. I love geometrical designs.
I have uploaded a very early version a friend of mine made (it even had a different title); this can be a starting point for you to work on, but I am more than open to suggestions and new ideas.
Should not have
• Please don't use my whole name, Iker Zurmendi is fine. I don't like ALL CAPITALS.

```html
<!DOCTYPE html>
<html lang="es">
<head>
<meta charset="utf-8">
<title>Queratocono — cubierta de tesis</title>
<link href="https://fonts.googleapis.com/css2?family=Cormorant+Garamond:wght@300;400;600;700&family=Crimson+Text:wght@400;600&display=swap" rel="stylesheet">
<style>
  :root{
    --stage:#231f20;
    --red:#c8161d;
    --blue:#2d4a9e;
    --blue-soft:#5d74b8;
    --white:#ffffff;
    --ink:#231f20;
    --rule:#777777;
  }
  *{margin:0;padding:0;box-sizing:border-box}
  html,body{width:1200px;height:1200px;overflow:hidden;background:var(--stage)}
  .spread{
    position:absolute;left:51px;top:253px;
    width:1252px;height:792px;
    transform:scale(0.877);transform-origin:0 0;
    overflow:hidden;background:var(--white);
  }
  .spread-shapes{position:absolute;inset:0}
  .back-copy{
    position:absolute;left:52px;top:50px;width:274px;
    color:var(--white);font-family:"Crimson Text",serif;
    font-size:13.2px;line-height:16.8px;
    hyphens:auto;-webkit-hyphens:auto;
  }
  .back-copy p{margin-bottom:5px}
  .author-photo{
    position:absolute;left:391px;top:51px;width:136px;height:136px;border-radius:50%;
    background:var(--white);display:flex;align-items:center;justify-content:center;
    font-family:"Crimson Text",serif;font-size:18px;color:var(--ink);
  }
  .author-bio{
    position:absolute;left:392px;top:220px;width:174px;
    color:var(--white);font-family:"Crimson Text",serif;font-size:12px;line-height:18px;
  }
  .spine-title,.spine-author{
    position:absolute;color:var(--white);font-family:"Crimson Text",serif;
    transform:rotate(90deg);transform-origin:0 0;white-space:nowrap;
  }
  .spine-title{left:636px;top:224px;font-size:8.4px;line-height:10px}
  .spine-author{left:632px;top:674px;font-size:13px}
  .university{
    position:absolute;left:1084px;top:34px;width:160px;text-align:center;
    font-family:"Crimson Text",serif;font-weight:600;font-size:11px;color:var(--red);
  }
  .university .seal{
    display:block;width:40px;height:40px;margin:0 auto 6px;border-radius:50%;
    border:1.5px solid var(--red);
  }
  .cover-title{
    position:absolute;left:692px;top:278px;color:var(--white);
    font-family:"Cormorant Garamond",serif;
  }
  .cover-title .lead{display:block;font-size:98px;font-weight:700;line-height:92px;letter-spacing:1px}
  .cover-title .light{display:block;font-size:29px;font-weight:300;line-height:36px}
  .cover-title .strong{display:block;font-size:31px;font-weight:700;line-height:37px}
  .cover-title .small{display:block;font-size:23px;font-weight:300;line-height:34px}
  .cover-title .disease{display:block;font-size:60px;font-weight:600;line-height:60px;letter-spacing:1px}
  .cover-author{
    position:absolute;right:30px;top:694px;
    font-family:"Cormorant Garamond",serif;font-size:46px;font-weight:400;color:var(--ink);
  }
</style>
</head>
<body>
<main class="spread">
  <svg class="spread-shapes" viewBox="0 0 1252 792" width="1252" height="792">
    <defs>
      <linearGradient id="eye-area-tone" x1="0" y1="0" x2="1" y2="1">
        <stop offset="0" stop-color="var(--blue-soft)"/>
        <stop offset="1" stop-color="var(--blue)"/>
      </linearGradient>
    </defs>
    <rect class="back-panel" x="0" y="0" width="366" height="792" fill="var(--red)"/>
    <rect class="spine-panel" x="366" y="0" width="361" height="792" fill="var(--blue)"/>
    <rect class="front-panel" x="727" y="0" width="525" height="792" fill="var(--white)"/>
    <rect class="front-corner" x="640" y="592" width="90" height="200" fill="var(--white)"/>
    <path class="quarter-disc" d="M667 202 H1237 A570 570 0 0 1 667 772 Z" fill="var(--red)"/>
    <circle class="lens" cx="879" cy="97" r="180" fill="var(--white)" stroke="var(--ink)" stroke-width="2" stroke-dasharray="7 5"/>
    <rect class="eye-illustration" x="747" y="52" width="268" height="140" rx="6" fill="url(#eye-area-tone)" role="img" aria-label="Ilustración de un ojo en azul"/>
    <polygon class="marker" points="1087,222 1165,222 1126,289" fill="var(--ink)"/>
    <polygon class="marker" points="1087,304 1165,304 1126,371" fill="var(--ink)"/>
    <line x1="900" y1="598" x2="1252" y2="598" stroke="var(--ink)" stroke-width="1"/>
    <line x1="725" y1="608" x2="1252" y2="608" stroke="var(--ink)" stroke-width="1"/>
    <line x1="640" y1="724" x2="964" y2="724" stroke="var(--rule)" stroke-width="1.2"/>
  </svg>

  <section class="back-copy">
    <p>Lorem ipsum dolor sit amet, consectetuer adipiscing elit, sed diam nonummy nibh euismod tincidunt ut laoreet dolore magna aliquam erat volutpat. Ut wisi enim ad minim veniam, quis nostrud exerci tation ullamcorper suscipit lobortis nisl ut aliquip ex ea commodo consequat. Duis autem vel eum iriure dolor in hendrerit in vulputate velit esse molestie consequat, vel illum dolore eu feugiat nulla facilisis at vero eros et accumsan et iusto odio dignissim qui blandit praesent luptatum zzril delenit augue duis dolore te feugait nulla facilisi.</p>
    <p>Lorem ipsum dolor sit amet, cons ectetuer adipiscing elit, sed diam nonummy nibh euismod tincidunt ut laoreet dolore magna aliquam erat volutpat. Ut wisi enim ad minim veniam, quis nostrud exerci tation ullamcorper suscipit lobortis nisl ut aliquip ex ea commodo consequat.</p>
    <p>Lorem ipsum dolor sit amet, consectetuer adipiscing elit, sed diam nonummy nibh euismod tincidunt ut laoreet dolore magna aliquam erat volutpat. Ut wisi enim ad minim veniam, quis nostrud exerci tation ullamcorper suscipit lobortis nisl ut aliquip ex ea commodo consequat. Duis autem vel eum iriure dolor in hendrerit in vulputate velit esse molestie consequat, vel illum dolore eu feugiat nulla facilisis at vero eros et accumsan et iusto odio dignissim qui blandit praesent luptatum zzril delenit augue duis dolore te feugait nulla facilisi.</p>
    <p>Lorem ipsum dolor sit amet, cons ectetuer adipiscing elit, sed diam nonummy nibh euismod tincidunt ut laoreet dolore magna aliquam erat volutpat. Ut wisi enim ad minim veniam, quis nostrud exerci tation ullamcorper suscipit lobortis nisl ut aliquip ex ea commodo consequat.</p>
    <p>Lorem ipsum dolor sit amet, consectetuer adipiscing elit, sed diam nonummy nibh euismod tincidunt ut laoreet dolore magna aliquam erat volutpat. Ut wisi enim ad minim veniam, quis nostrud exerci</p>
  </section>

  <div class="author-photo">authors photo</div>
  <p class="author-bio">Iker Zurmendi, MD, es un Oftalmólogo Subespecialista en Cirugía Refractiva de la Universidad Tecnológica Cordillerana (Colombia) y la Universidad de Montehierro (España). Actualmente se desempeña como miembro del Departamento de Córnea y Cirugía Refractiva de la Clínica de Oftalmología Miraluz y como director de su propia compañía de emprendimiento médico Silver Heron Surgical</p>

  <p class="spine-title">Diseño, desarrollo y validación de una encuesta para evaluar el compromiso visual<br>y emocional subjetivos en pacientes con Queratocono</p>
  <p class="spine-author">Iker Zurmendi</p>

  <div class="university"><span class="seal"></span>Universidad de Montehierro</div>

  <h1 class="cover-title">
    <span class="lead">Diseño,</span>
    <span class="light">desarrollo y validación</span>
    <span class="strong">de una encuesta para</span>
    <span class="strong">evaluar el compromiso visual</span>
    <span class="small">y emocional subjetivos en pacientes con</span>
    <span class="disease">Queratocono</span>
  </h1>
  <p class="cover-author">Iker Zurmendi</p>
</main>
</body>
</html>
```